Brisk Coatings business card for residential and commercial painting

A clean, professional design. Easy to read
Eye catching and elegant
Front could have some color variations
On the back of card I would like all black with signature logo

*Attached is my current business card and the items I want displayed

Contact Information for Business Card

Email, phone number, website, and owner name

Font styles to use
Serif

Requirements
Must have
• My logo with cool design and perhaps some paint splatter

```html
<!DOCTYPE html>
<html lang="en">
<head>
<meta charset="utf-8">
<title>Brisk Coatings – Business Card</title>
<link href="https://fonts.googleapis.com/css2?family=Oswald:wght@500&family=Roboto:wght@400;500;700&display=swap" rel="stylesheet">
<style>
  :root {
    --backdrop: #e9e9ea;
    --card-dark: #343437;
    --paper: #f7f7f7;
    --rule: #b9b9bb;
    --mark-grey: #8d8d91;
    --ink: #2b2b2d;
    --brand-blue: #1565b4;
    --tagline-blue: #2a8be0;
    --white: #ffffff;
  }
  * { margin: 0; padding: 0; box-sizing: border-box; }
  html, body { width: 1200px; height: 1200px; overflow: hidden; }
  body { background: var(--backdrop); position: relative; font-family: "Roboto", Arial, sans-serif; }

  .card {
    position: absolute;
    left: 303px;
    width: 594px;
    height: 348px;
    border-radius: 22px;
    overflow: hidden;
  }

  /* Front */
  .card-front { top: 198px; background: var(--paper); }
  .front-band {
    position: absolute; left: 0; top: 0; width: 100%; height: 208px;
    background: var(--card-dark);
    display: flex; align-items: center; justify-content: center;
  }
  .front-wordmark {
    font-family: "Oswald", "Arial Narrow", sans-serif;
    font-weight: 500; font-size: 54px; letter-spacing: 1px;
    color: var(--mark-grey);
    text-transform: uppercase;
  }
  .note-line {
    position: absolute; left: 35px; right: 35px; height: 2px;
    background: var(--rule);
  }
  .note-line.l1 { top: 244px; }
  .note-line.l2 { top: 279px; }
  .note-line.l3 { top: 314px; }

  /* Back */
  .card-back { top: 636px; background: var(--card-dark); }
  .paint-stroke { position: absolute; left: 22px; top: 24px; width: 548px; height: 200px; }
  .owner { position: absolute; right: 326px; top: 96px; text-align: right; }
  .owner-name { color: var(--brand-blue); font-weight: 500; font-size: 23px; line-height: 1; }
  .owner-role { color: var(--ink); font-size: 15.5px; margin-top: 10px; }
  .contact-list { position: absolute; left: 296px; top: 92px; list-style: none; }
  .contact-list li {
    display: flex; align-items: center; gap: 10px;
    font-size: 15.5px; color: var(--ink); height: 21px;
  }
  .contact-list svg { width: 16px; height: 14px; flex: none; }
  .brush-art {
    position: absolute; left: 500px; top: 164px; width: 46px; height: 112px;
    background: linear-gradient(160deg, #1a6fc2, #12549a);
    border-radius: 8px 8px 18px 18px;
  }
  .back-wordmark {
    position: absolute; left: 60px; top: 250px;
    font-family: "Oswald", "Arial Narrow", sans-serif;
    font-weight: 500; font-size: 30px; letter-spacing: 0.5px;
    color: var(--white); text-transform: uppercase; line-height: 1;
  }
  .tagline {
    position: absolute; left: 144px; top: 291px;
    color: var(--tagline-blue); font-size: 15px;
  }
</style>
</head>
<body>

<section class="card card-front" aria-label="Card front">
  <div class="front-band">
    <span class="front-wordmark">Brisk Coatings</span>
  </div>
  <div class="note-line l1"></div>
  <div class="note-line l2"></div>
  <div class="note-line l3"></div>
</section>

<section class="card card-back" aria-label="Card back">
  <svg class="paint-stroke" viewBox="0 0 548 200" preserveAspectRatio="none" aria-hidden="true">
    <path fill="#f8f8f8" d="M20 6 L90 2 L160 8 L240 3 L320 7 L400 2 L470 6 L520 4 L532 22 L528 50 L540 80 L532 112 L544 150 L530 176 L536 196 L470 192 L400 198 L320 194 L240 199 L160 193 L90 198 L22 194 L28 170 L14 140 L22 108 L4 76 L16 48 L8 24 Z"/>
  </svg>

  <div class="owner">
    <div class="owner-name">Marco "MJ"</div>
    <div class="owner-role">Owner - Licensed &amp; Insured</div>
  </div>

  <ul class="contact-list">
    <li>
      <svg viewBox="0 0 16 14" aria-hidden="true"><path fill="var(--brand-blue)" d="M1 4 Q8 -1 15 4 L13 6 L11 4.5 L5 4.5 L3 6 Z M4 7 L12 7 L14 13 L2 13 Z"/><circle cx="8" cy="10" r="1.6" fill="#fff"/></svg>
      <span>555-014-2387</span>
    </li>
    <li>
      <svg viewBox="0 0 16 14" aria-hidden="true"><rect x="1" y="2" width="14" height="10" fill="var(--brand-blue)"/><path d="M1 2 L8 8 L15 2" stroke="#fff" stroke-width="1.3" fill="none"/></svg>
      <span>hello@briskcoatings.com</span>
    </li>
    <li>
      <svg viewBox="0 0 16 14" aria-hidden="true"><circle cx="8" cy="7" r="6" fill="var(--brand-blue)"/><path d="M2 7 H14 M8 1 V13 M3.5 4 H12.5 M3.5 10 H12.5" stroke="#fff" stroke-width="0.8" fill="none"/></svg>
      <span>www.briskcoatings.com</span>
    </li>
  </ul>

  <div class="brush-art" role="img" aria-label="Blue paintbrush illustration"></div>

  <div class="back-wordmark">Brisk Coatings</div>
  <div class="tagline">Colour Done Right</div>
</section>

</body>
</html>
```